Maple Lantern Productions web site

I need to build a website for a new company I am launching next month. Maple Lantern Productions is a company based in New England that provides sound, lighting, and audio visual services to weddings, corporate, and any other cusomer base looking for quality service for a fair price. Looking for somebody to do a full site not just the image files. I am looking to keep the colors of my logo (orange and black) and possibly grey and white. I am looking to build my site very similar to brightvaleevents.example, which is owned by a friend of mine. I like how he has the big pictures that load in to the site and the basic menu items. I'll need a gallery of photos. The designs should communicate quality, value and trust.
My website address is maplelanternco.example.
Updates

Hi and thanks to everyone for posting such great ideas for our new design.I have some items that I'd like to ask you all to focus on in your revisions.I like how http://www.brightvaleevents.example/ website has five or six high res pictures that change in a slideshow format with a caption that loads in for each one for the different types of services. Try and capture pics like these and with teh same headings as he has. The basic menu designs have been interesting.I am more fond of the menus that are more white with some orange as I dont want it to be too dark. I'm curious to see how your galleries will work and if i'll be able to edit the pages myself? I have some more info on the company for you to fill in:website address is ciderhouseco.comemail: info@ciderhouseco.comaddress: Maple Lantern Productions57 Littlefield StreetAvon, MA 02417"New England's finest DJ's, lighting and sound, video and more. Creating memories one perfect event at a time."Put this under the loading pictures as a tagline.About Cider HouseCider House Productions is a collection of New England's finest talent, ready to make your next event the one you've dreamed of. We have the skills and expertise to deliver your vision of your perfect event. From elegant weddings to themed mitzvah's, corporate av, videography and detail lighting, we offer all of the elements to make your event a success. Added Wednesday, March 1, 2017

Designer's Please also make sure that your design flows well on any device it is being viewed on as well. Thanks. Added Wednesday, March 1, 2017

Project Deadline Extended Reason: Hello designerThank you all very much for your hard work on our project. Im sorry but i need to extend the date of my project. Our parent conpany Rook Nine Prodactions sponsors Bay Youth Assemblies and we are currently at their leadership conference on the Cape. I will be back in on Monday and with your help will get this finished by Thursday the 16th. Thanks Added Thursday, March 9, 2017

Project Deadline Extended Reason: One of the designers is not responding so I now have to make revisions with other designers. I hope to get this website done over the weekends so please get your revisions as soon as possible. Thank you. I am also upgrading the budget another $75 to hopefully get some more interest on my project. Added Wednesday, March 15, 2017

Target Market(s)

Wedding - Corporate -

Industry/Entity Type

It Company

Coding

Coded - Design and coding required

Number of Pages Required

5+ page

Font styles to use
Sans Serif

Requirements
Must have
• Photo Gallery - I want to be able to edit it myself
Nice to have
• I like the look of my friends website brightvaleevents.example

```html
<!DOCTYPE html>
<html lang="en">
<head>
<meta charset="utf-8">
<title>Maple Lantern Productions</title>
<link href="https://fonts.googleapis.com/css2?family=Open+Sans:wght@300;400;600;700&display=swap" rel="stylesheet">
<style>
:root{
  --orange:#f15a24;
  --orange-dark:#e04e1b;
  --ink:#1c1c1c;
  --text:#555;
  --muted:#8a8a8a;
  --line:#dcdcdc;
  --white:#fff;
  --grey-bg:#ebebeb;
  --footer:#1b1b1b;
}
*{box-sizing:border-box;margin:0;padding:0}
html,body{width:1200px;height:4401px;overflow:hidden}
body{font-family:"Open Sans",Arial,sans-serif;color:var(--text);background:var(--white);position:relative}
section,header,footer{position:relative;width:1200px;overflow:hidden}
.abs{position:absolute}
.photo{position:absolute}

/* header */
.site-header{height:117px;background:var(--white)}
.brand{left:126px;top:24px;display:flex;align-items:center;gap:14px}
.brand-mark{width:66px;height:66px;border-radius:50%;background:var(--orange)}
.brand-name{font-weight:700;color:var(--ink);font-size:23px;line-height:24px;letter-spacing:.5px;text-transform:uppercase}
.brand-name small{display:block;font-size:23px;font-weight:700}
.phone{right:134px;top:16px;font-size:18px;font-weight:600;color:var(--ink);display:flex;align-items:center;gap:8px}
.main-nav{left:414px;top:53px;display:flex;align-items:center}
.main-nav a{font-size:14px;color:#444;text-decoration:none;text-transform:uppercase;letter-spacing:.4px;margin-right:34px;line-height:38px}
.main-nav a.active{border:2px solid var(--orange);padding:0 22px;color:var(--ink);font-weight:600;margin-right:54px}

/* hero */
.hero{height:523px}
.hero .photo{inset:0;background:radial-gradient(ellipse at 50% 35%,#b9b2b8 0%,#5a4f66 30%,#241b33 60%,#0c0a12 100%)}
.hero-copy{left:0;right:0;top:300px;text-align:center;color:var(--white)}
.hero-copy h1{font-weight:400;font-size:35px;letter-spacing:.5px;text-transform:uppercase}
.hero-copy p{font-size:44px;font-weight:400;text-transform:uppercase;margin-top:2px}
.slider-dots{left:525px;top:588px;display:flex;gap:10px}
.slider-dots span{width:40px;height:3px;background:rgba(255,255,255,.5)}
.slider-dots span.on{background:var(--white)}

/* welcome */
.welcome{height:410px}
.welcome .photo{left:155px;top:32px;width:330px;height:330px;border-radius:50%;background:radial-gradient(circle at 50% 45%,#f5c9ef 0%,#c54fc0 40%,#4c2360 100%)}
.welcome-copy{left:522px;top:60px;width:540px}
.welcome-copy h2{font-size:26px;font-weight:600;color:var(--ink);text-transform:uppercase}
.welcome-copy h2 span{color:var(--orange)}
.welcome-copy p{font-size:13px;line-height:20px;color:var(--muted);margin-top:14px}
.btn-outline{display:inline-block;margin-top:26px;border:1.5px solid #333;padding:0 40px;line-height:42px;font-size:13px;color:var(--ink);text-transform:uppercase}

/* orange banners */
.band{background:var(--orange);color:var(--white);text-align:center;height:110px}
.band h2{font-size:27px;font-weight:600;line-height:110px;text-transform:uppercase}
.notch{position:absolute;left:582px;width:0;height:0;border-left:18px solid transparent;border-right:18px solid transparent}

/* services */
.services{height:1158px}
.service{position:absolute}
.service h3{font-size:32px;font-weight:300;color:var(--orange)}
.service p{font-size:13px;line-height:20px;color:var(--muted);margin-top:14px}
.btn-fill{display:inline-block;background:var(--orange);color:var(--white);font-size:13px;text-transform:uppercase;line-height:38px;padding:0 26px;margin-top:18px}
.rule{position:absolute;left:138px;width:924px;height:1px;background:var(--line)}

/* about */
.about{height:595px}
.about .photo{inset:0;background:radial-gradient(ellipse at 50% 10%,#3d5a86 0%,#1c2840 35%,#0b0f18 75%)}
.about-copy{left:200px;right:200px;top:60px;text-align:center;color:var(--white)}
.about-copy h2{font-size:30px;font-weight:600;text-transform:uppercase}
.about-copy p{font-size:14px;line-height:22px;margin-top:10px}
.team{left:130px;top:290px;display:flex;width:940px;justify-content:space-between}
.member{width:220px;text-align:center;color:var(--white)}
.member .avatar{width:132px;height:132px;border-radius:50%;border:4px solid var(--white);background:linear-gradient(160deg,#c9b9a8,#6e5a4a);margin:0 auto}
.member h4{font-size:14px;font-weight:600;margin-top:20px;text-transform:uppercase}
.member p{font-size:12px;line-height:16px;margin-top:6px;color:#ddd}

/* gallery */
.gallery{height:505px}
.gallery h2{text-align:center;font-size:27px;font-weight:600;color:var(--ink);padding-top:48px;text-transform:uppercase}
.gallery .photo{width:223px;height:158px}

/* testimonials */
.testimonials{height:396px;background:var(--orange)}
.testimonials h2{text-align:center;color:var(--white);font-size:27px;font-weight:600;padding-top:47px;text-transform:uppercase}
.quote{position:absolute;top:109px;width:393px;height:155px;background:#e8361c;color:var(--white);font-size:13px;font-style:italic;line-height:19px;text-align:center;padding:24px 40px}
.quote-avatar{position:absolute;top:231px;width:66px;height:66px;border-radius:50%;border:3px solid var(--white);background:linear-gradient(160deg,#c9b0a0,#6b4c3c)}
.quote-author{position:absolute;top:302px;width:393px;text-align:center;color:var(--white);font-size:13px;font-weight:600}

/* contact */
.contact{height:426px;background:var(--grey-bg)}
.contact h2{text-align:center;font-size:27px;font-weight:600;color:var(--ink);padding-top:80px;text-transform:uppercase}
.field{position:absolute;background:var(--white);border:1px solid #bbb;font-size:13px;color:#666;padding:10px 14px}
.btn-submit{position:absolute;left:513px;top:323px;width:141px;height:38px;background:var(--orange);color:var(--white);font-size:14px;text-transform:uppercase;line-height:38px;text-align:center}

/* footer */
.site-footer{height:161px;background:var(--footer);color:var(--white)}
.foot-nav{left:106px;top:50px;display:flex;gap:38px}
.foot-nav a{color:var(--white);text-decoration:none;font-size:13px;font-weight:600;text-transform:uppercase}
.copyright{left:106px;top:91px;font-size:12px;color:#888}
.social{left:904px;top:52px;display:flex;gap:8px}
.social span{width:31px;height:31px;border:1.5px solid var(--white)}
</style>
</head>
<body>

<header class="site-header">
  <div class="brand abs">
    <div class="brand-mark"></div>
    <div class="brand-name">Maple Lantern<small>Productions</small></div>
  </div>
  <div class="phone abs">
    <svg width="18" height="18" viewBox="0 0 24 24"><rect width="24" height="24" rx="3" fill="#f15a24"/><path d="M8 5l2 3-1.5 1.5c.8 1.8 2.2 3.2 4 4L14 12l3 2-1 3c-5 0-9-4-9-9z" fill="#fff"/></svg>
    555-204-7731
  </div>
  <nav class="main-nav abs">
    <a class="active" href="#">Home</a>
    <a href="#">About Us</a>
    <a href="#">Services</a>
    <a href="#">Gallery</a>
    <a href="#">Team</a>
    <a href="#">Review</a>
    <a href="#">Contact</a>
  </nav>
</header>

<section class="hero">
  <div class="photo" role="img" aria-label="Concert stage with bright spotlights over a crowd"></div>
  <div class="hero-copy abs">
    <h1>Maple Lantern Productions</h1>
    <p>Sound, Lightingand Audio Visual</p>
  </div>
  <div class="slider-dots abs" style="top:471px"><span class="on"></span><span></span><span></span></div>
</section>

<section class="welcome">
  <div class="photo" role="img" aria-label="Bride and groom dancing under pink lights"></div>
  <div class="welcome-copy abs">
    <h2>Welcome <span>Maple Lantern</span></h2>
    <p>Fusce ultricies orci ac feugiat suscipit leo massa sodales velit et scelerisque mi tortor at ipsum cligula augue bibendum accumsan vestibulum ut commodo a mi Morbi</p>
    <p>aenare gravida elit Integer congue augue et malesuada iaculis ipsum dui aliquet felis at cursus magna nisl nec elit Praesent elementum elit at tellus nec ultricies sit amet porttitor mattis enim in massa</p>
    <span class="btn-outline">Read More</span>
  </div>
</section>

<section class="band">
  <h2>Our Services</h2>
</section>

<section class="services">
  <div class="notch" style="top:0;border-top:20px solid var(--orange)"></div>

  <div class="service" style="left:138px;top:90px;width:440px">
    <h3>Sound &amp; Lighting</h3>
    <p>Fusce ultricies orci ac feugiat suscipit leo massa sodales velit et scelerisque mi tortor at ipsum cligula</p>
    <p>aenare gravida elit Integer congue augue et malesuada iaculis ipsum dui aliquet felis at cursus magna nisl nec elit Praesent elementum elit at tellus nec ultricies sit amet porttitor mattis enim in massa</p>
    <span class="btn-fill">Read More</span>
  </div>
  <div class="photo" style="left:631px;top:66px;width:408px;height:256px;background:radial-gradient(ellipse at 50% 20%,#fff3b0 0%,#f0a020 35%,#8a3a0c 70%,#2a1206 100%)" role="img" aria-label="Crowd with raised hands under golden stage lights"></div>

  <div class="rule" style="top:390px"></div>

  <div class="photo" style="left:132px;top:433px;width:411px;height:258px;background:radial-gradient(circle at 45% 55%,#e7c9ff 0%,#9b3fd0 25%,#3a1650 60%,#120818 100%)" role="img" aria-label="DJ turntable lit in purple"></div>
  <div class="service" style="left:610px;top:470px;width:450px">
    <h3>Audio Visual services</h3>
    <p>Fusce ultricies orci ac feugiat suscipit leo massa sodales velit et scelerisque mi tortor at ipsum cligula</p>
    <p>aenare gravida elit Integer congue augue et malesuada iaculis ipsum dui aliquet felis at cursus magna nisl nec elit Praesent elementum elit at tellus nec ultricies sit amet porttitor mattis enim in massa</p>
    <span class="btn-fill">Read More</span>
  </div>

  <div class="rule" style="top:753px"></div>

  <div class="service" style="left:161px;top:810px;width:440px">
    <h3>Wedding &amp; Events</h3>
    <p>Fusce ultricies orci ac feugiat suscipit leo massa sodales velit et scelerisque mi tortor at ipsum cligula</p>
    <p>aenare gravida elit Integer congue augue et malesuada iaculis ipsum dui aliquet felis at cursus magna nisl nec elit Praesent elementum elit at tellus nec ultricies sit amet porttitor mattis enim in massa</p>
    <span class="btn-fill">Read More</span>
  </div>
  <div class="photo" style="left:651px;top:797px;width:411px;height:258px;background:linear-gradient(135deg,#e04aa0 0%,#c7d6f0 45%,#6a3aa0 100%)" role="img" aria-label="Wedding couple under falling confetti"></div>
</section>

<section class="about">
  <div class="photo" role="img" aria-label="Dark stage with blue spotlights"></div>
  <div class="notch" style="top:0;border-top:20px solid var(--white)"></div>
  <div class="about-copy abs">
    <h2>About Us</h2>
    <p>Fusce ultricies orci ac feugiat suscipit leo massa sodales velit et scelerisque mi tortor at ipsum cligula augue bibendum accumsan vestibulum ut commodo a mi Morbi ornare gravida</p>
    <p>elit Integer congue augue et malesuada iaculis ipsum dui aliquet felis at cursus magna nisl nec elit Praesent elementum elit at tellus nec ultricies sit amet porttitor mattis enim in massa libero interdum nec interdum vel blandit sed nulla is ullamcorper est eget tempor cursus neque mi</p>
  </div>
  <div class="team abs">
    <div class="member"><div class="avatar" role="img" aria-label="Team member portrait"></div><h4>Member Name</h4><p>mel porttitor mattis enim in massa libero interdum nec interdum vel blandit</p></div>
    <div class="member"><div class="avatar" role="img" aria-label="Team member portrait"></div><h4>Member Name</h4><p>mel porttitor mattis enim in massa libero interdum nec interdum vel blandit</p></div>
    <div class="member"><div class="avatar" role="img" aria-label="Team member portrait"></div><h4>Member Name</h4><p>mel porttitor mattis enim in massa libero interdum nec interdum vel blandit</p></div>
    <div class="member"><div class="avatar" role="img" aria-label="Team member portrait"></div><h4>Member Name</h4><p>mel porttitor mattis enim in massa libero interdum nec interdum vel blandit</p></div>
  </div>
</section>

<section class="gallery">
  <h2>Our Gallery</h2>
  <div class="photo" style="left:138px;top:109px;background:linear-gradient(160deg,#e8e2dc,#a89a8c)" role="img" aria-label="Decorated wedding reception hall"></div>
  <div class="photo" style="left:373px;top:109px;background:linear-gradient(160deg,#f08ad0,#7a2a8a)" role="img" aria-label="Couple dancing in pink light"></div>
  <div class="photo" style="left:607px;top:109px;background:linear-gradient(160deg,#e8d2a8,#8a6a3a)" role="img" aria-label="Banquet tables in warm light"></div>
  <div class="photo" style="left:842px;top:109px;background:linear-gradient(160deg,#d8c8a0,#6a5030)" role="img" aria-label="Ballroom with chandeliers"></div>
  <div class="photo" style="left:138px;top:279px;background:linear-gradient(160deg,#b070e0,#3a1a6a)" role="img" aria-label="Event tent lit in purple"></div>
  <div class="photo" style="left:373px;top:279px;background:linear-gradient(160deg,#c090e8,#4a2a7a)" role="img" aria-label="Reception room with purple uplighting"></div>
  <div class="photo" style="left:607px;top:279px;background:linear-gradient(160deg,#8a8aff,#2a2a8a)" role="img" aria-label="Dance floor in blue and violet light"></div>
  <div class="photo" style="left:842px;top:279px;background:linear-gradient(160deg,#9a70d0,#2a1a4a)" role="img" aria-label="Wedding hall with purple lights"></div>
</section>

<section class="testimonials">
  <h2>Testimonials</h2>
  <div class="quote" style="left:185px">Morbi ornare gravida elit Integer congue augue et malesuada iaculis ipsum dui aliquet felis at cursus magna nisl nec elit Praesent elementum elit at tellus nec ultricies sit amet porttitor mattis</div>
  <div class="quote" style="left:619px">Aenean tempor mi a ultricies massa est sed nisl Class aptent taciti sociosqu ad litora torquent per conubia nostra per inceptos hymenaeos Proin nulla eros nonummy luctus dictum eget fermentum et lorem</div>
  <div class="quote-avatar" style="left:348px" role="img" aria-label="Client portrait"></div>
  <div class="quote-avatar" style="left:782px" role="img" aria-label="Client portrait"></div>
  <div class="quote-author" style="left:185px">By Author Name, City Location</div>
  <div class="quote-author" style="left:619px">By Author Name, City Location</div>
</section>

<section class="contact">
  <div class="notch" style="top:0;border-top:22px solid var(--orange)"></div>
  <h2>Want to Contact Us</h2>
  <div class="field" style="left:153px;top:138px;width:284px;height:45px">Your Name</div>
  <div class="field" style="left:452px;top:138px;width:279px;height:45px">Email address</div>
  <div class="field" style="left:745px;top:138px;width:282px;height:45px">Phone</div>
  <div class="field" style="left:153px;top:194px;width:874px;height:105px">Message</div>
  <div class="btn-submit">Submit</div>
</section>

<footer class="site-footer">
  <nav class="foot-nav abs">
    <a href="#">Home</a><a href="#">About Us</a><a href="#">Services</a><a href="#">Gallery</a><a href="#">Team</a><a href="#">Review</a><a href="#">Contact</a>
  </nav>
  <div class="copyright abs">© 2017 Company Name. All right reserved. &nbsp; Terms of Use &nbsp;|&nbsp; Privacy Policy</div>
  <div class="social abs"><span></span><span></span><span></span><span></span></div>
</footer>

</body>
</html>
```